Lo Mara Menu Design Project

This project is pretty straight forward. You will be given 3 files which include the following:
1. Our proposed menu
2. Our Company logo
3. A sample menu on what we are looking for design wise

Your job is to create a visually pleasing menu that is simple, clean and fresh. Please refer to our home website for additional information. (www.lomara-eats.com) Must be in eps or equivalent format.

Target Market(s)

20s to 40s

Industry/Entity Type

It Company

Requirements
Must have
• Company log
Must be in EPS format

```html
<!DOCTYPE html>
<html lang="en">
<head>
<meta charset="utf-8">
<title>Lo Mara Menu</title>
<link rel="stylesheet" href="https://fonts.googleapis.com/css2?family=Tinos:wght@700&family=PT+Sans:wght@400&display=swap">
<style>
  :root {
    --backdrop: #6b4128;
    --panel: #151515;
    --panel-grain: #1d1d1d;
    --heading: #ffffff;
    --text: #e6e6e6;
    --mark: rgba(150, 28, 28, 0.28);
    --photo-pasta-a: #c0502a;
    --photo-pasta-b: #e7c08a;
    --photo-noodle-a: #c9a877;
    --photo-noodle-b: #6b5238;
    --photo-beef-a: #3d2a1f;
    --photo-beef-b: #3f7a2e;
  }
  * { margin: 0; padding: 0; box-sizing: border-box; }
  html, body {
    width: 1097px; height: 1200px; overflow: hidden;
    background: var(--backdrop);
  }
  .menu {
    position: absolute; left: 122px; top: 29px;
    width: 852px; height: 1142px;
    background:
      repeating-linear-gradient(90deg, var(--panel) 0 3px, var(--panel-grain) 3px 5px, var(--panel) 5px 9px),
      var(--panel);
    overflow: hidden;
    font-family: "PT Sans", sans-serif;
    color: var(--text);
  }
  .photo { position: absolute; top: 43px; height: 174px; }
  .photo--pasta { left: 0; width: 319px; border-radius: 0 0 60% 0 / 0 0 30% 0;
    background: radial-gradient(ellipse at 45% 40%, var(--photo-pasta-a), var(--photo-pasta-b) 70%, #f2efe9 90%); }
  .photo--noodles { left: 316px; width: 365px;
    background: radial-gradient(ellipse at 50% 50%, var(--photo-noodle-a), var(--photo-noodle-b) 85%); opacity: .9; }
  .photo--beef { left: 667px; width: 185px; border-radius: 30% 0 0 30%;
    background: radial-gradient(ellipse at 50% 50%, var(--photo-beef-a), var(--photo-beef-b) 60%, #f4f4f2 85%); }
  .brand-mark {
    position: absolute; left: 0; width: 100%; top: 300px;
    text-align: center; font-family: "Tinos", serif; font-weight: 700;
    font-size: 210px; line-height: 230px; color: var(--mark); letter-spacing: 8px;
  }
  .section-title {
    position: absolute; left: 0; width: 100%; text-align: center;
    font-family: "PT Sans", sans-serif; font-size: 40px; font-weight: 400;
    color: var(--heading); letter-spacing: 1px;
  }
  .item {
    position: absolute; width: 290px; margin-left: -145px; text-align: center;
  }
  .item__name, .item__price {
    font-family: "Tinos", serif; font-weight: 700; font-size: 17px;
    line-height: 20px; color: var(--heading);
  }
  .item__desc { margin-top: 8px; font-size: 13px; line-height: 16px; }
  .item--wide { width: 720px; margin-left: -360px; }
</style>
</head>
<body>
<main class="menu">
  <div class="photo photo--pasta" role="img" aria-label="Photo of pasta with meat sauce on a white plate"></div>
  <div class="photo photo--noodles" role="img" aria-label="Photo of stir-fried noodles with shrimp"></div>
  <div class="photo photo--beef" role="img" aria-label="Photo of beef with green beans on a white plate"></div>

  <div class="brand-mark" aria-hidden="true">LO<br>MARA</div>

  <h2 class="section-title" style="top:250px">DIM SUM</h2>

  <div class="item" style="left:167px;top:322px">
    <div class="item__name">Pan-Fried Potstickers</div>
    <div class="item__price">$ 6.50</div>
    <p class="item__desc">Five pan-Fried potstickers with<br>chicken or pork.<br>Served with apricot dipping sauce</p>
  </div>
  <div class="item" style="left:167px;top:451px">
    <div class="item__name">Spring Rolls</div>
    <div class="item__price">$ 4.50</div>
    <p class="item__desc">Two chicken or vegetable<br>spring rolls. Served with apricot<br>dipping sauce</p>
  </div>
  <div class="item" style="left:167px;top:591px">
    <div class="item__name">Shrimp Toast</div>
    <div class="item__price">$ 5.95</div>
    <p class="item__desc">Four pieces of fried toast with<br>shrimp, onions, bamboo shoots, and<br>water chestnuts. Served with apricot<br>dipping sauce.</p>
  </div>

  <div class="item" style="left:449px;top:365px">
    <div class="item__name">Szechuan Dumplings</div>
    <div class="item__price">$ 6.25</div>
    <p class="item__desc">Five chicken dumplings<br>tossed in a spicy cilantro<br>sauce.</p>
  </div>
  <div class="item item--wide" style="left:449px;top:497px;width:300px;margin-left:-150px">
    <div class="item__name">Wonton Stars</div>
    <div class="item__price">$ 7.25</div>
    <p class="item__desc">Five crispy wonton skins filled<br>with real crab and seasoned cream cheese.<br>Served with sweet and sour dipping sauce.</p>
  </div>
  <div class="item" style="left:449px;top:635px">
    <div class="item__name">Shu Mai</div>
    <div class="item__price">$ 5.95</div>
    <p class="item__desc">Six steamed open-Face dumplings<br>with pork<br>shrimp, and mushrooms.</p>
  </div>

  <div class="item" style="left:674px;top:322px">
    <div class="item__name">Steamed Dumplings</div>
    <div class="item__price">$ 6.50</div>
    <p class="item__desc">Five steamed dumplings with<br>chicken, or vegetables.<br>Served with apricot dipping sauce.</p>
  </div>
  <div class="item" style="left:674px;top:451px">
    <div class="item__name">Bao</div>
    <div class="item__price">$ 5.95</div>
    <p class="item__desc">Three fluffy steamed chinese<br>buns filled with barbeque<br>pork.</p>
  </div>
  <div class="item" style="left:674px;top:591px">
    <div class="item__name">Gift Wrapped Chicken</div>
    <div class="item__price">$5.95</div>
    <p class="item__desc">Six chicken breast tenders marinated<br>in soy sauce<br>sesame oil, and cilantro.</p>
  </div>

  <h2 class="section-title" style="top:781px">STARTERS</h2>

  <div class="item" style="left:190px;top:857px">
    <div class="item__name">Lightly Battered Calamari Strips</div>
    <div class="item__price">$ 5.95</div>
    <p class="item__desc">Six calamari strips, lightly battered<br>with a garlic ginger aioli.</p>
  </div>
  <div class="item" style="left:425px;top:883px">
    <div class="item__name">Edamame</div>
    <div class="item__price">$ 4.00</div>
    <p class="item__desc">Steamed Soybean Pods.</p>
  </div>
  <div class="item" style="left:674px;top:857px">
    <div class="item__name">Lo Mara Crab Cake's</div>
    <div class="item__price">$11.95</div>
    <p class="item__desc">Jumbo lump Maryland crab meat<br>with seasoned<br>with our Lo Mara spice blend.<br>Topped with a kick of spicy aioli.</p>
  </div>

  <div class="item item--wide" style="left:420px;top:1001px">
    <div class="item__name">Dim Sum And Then Sum &nbsp;&nbsp;(Lunch / Dinner)</div>
    <div class="item__price">$ 14.95 / 18.95</div>
    <p class="item__desc">Choose three / four half orders: Potstickers, steamed dumplings, szechwan dumplings,<br>spring roll, shrimp toast, chinese chicken salad, hot &amp; sour soup, wonton soup, or mushu,<br>For Shrimp fried rice, beef fried rice, or mushu shrimp, add $1.00.</p>
  </div>
</main>
</body>
</html>
```